New Business Card Design Project

Use the flyer uploaded and website www.brightoakbuilders.com for inspiration.
List Our Services on Backside of business cards
Marcus Delling
Harborline Builders Inc.
Licensed General Contractors
858-471-6093

Contact Information for Business Card

Use the flyer uploaded and website www.brightoakbuilders.com for inspiration. List Our Services on Backside of business cards Marcus Delling Harborline Builders Inc. Licensed General Contractors 858-471-6093

```html
<!DOCTYPE html>
<html lang="en">
<head>
<meta charset="utf-8">
<title>Harborline Builders Business Card</title>
<link href="https://fonts.googleapis.com/css2?family=Roboto:wght@400;500;700;900&display=swap" rel="stylesheet">
<style>
  :root {
    --stage: #232325;
    --card: #1f1f23;
    --red: #e8202a;
    --blue: #4d7fd6;
    --white: #ffffff;
    --muted: #e9e9ee;
  }
  * { box-sizing: border-box; margin: 0; padding: 0; }
  html, body {
    width: 1200px; height: 780px; overflow: hidden;
    background: var(--stage);
    font-family: "Roboto", Arial, sans-serif;
  }
  .stage {
    width: 1200px; height: 780px;
    display: flex; align-items: center; justify-content: center; gap: 36px;
  }
  .card {
    position: relative;
    width: 560px; height: 320px;
    background: var(--card);
    border-bottom: 7px solid var(--red);
    box-shadow: 0 14px 30px rgba(0,0,0,.55);
    overflow: hidden;
  }

  /* Front: brand + services */
  .brand {
    position: absolute; left: 44px; top: 150px;
    display: flex; align-items: center; gap: 12px;
  }
  .brand-mark { width: 14px; height: 14px; background: var(--white); flex: none; }
  .brand-name {
    color: var(--white); font-weight: 400; font-size: 24px; line-height: 1.15;
    letter-spacing: 2px; text-transform: uppercase;
  }
  .services { position: absolute; left: 300px; top: 40px; }
  .services-guarantee {
    color: var(--red); font-weight: 900; font-size: 15px;
    line-height: 1.12; text-transform: uppercase;
  }
  .services-heading {
    color: var(--blue); font-weight: 900; font-size: 15px;
    text-transform: uppercase; margin: 2px 0 8px;
  }
  .service-list { list-style: none; }
  .service-item {
    display: flex; align-items: center; gap: 8px;
    color: var(--muted); font-size: 11.5px; font-weight: 500; line-height: 21px;
  }
  .tick { width: 13px; height: 13px; flex: none; }

  /* Back: contact */
  .person { position: absolute; left: 36px; top: 168px; }
  .person-name { color: var(--red); font-weight: 900; font-size: 40px; line-height: 1; }
  .person-title { color: var(--white); font-size: 15px; font-weight: 500; margin-top: 4px; }
  .divider {
    position: absolute; left: 334px; top: 72px;
    width: 2px; height: 96px; background: var(--red);
  }
  .contact-list { position: absolute; left: 352px; top: 80px; list-style: none; }
  .contact-item {
    display: flex; align-items: center; gap: 8px;
    color: var(--white); font-size: 12.5px; font-weight: 500; line-height: 26px;
    white-space: nowrap;
  }
  .contact-icon { width: 13px; height: 13px; flex: none; }
  .company {
    position: absolute; right: 40px; bottom: 30px;
    color: var(--white); font-size: 14px; font-weight: 500;
  }
</style>
</head>
<body>
<main class="stage">

  <section class="card card-front">
    <div class="brand">
      <span class="brand-mark"></span>
      <span class="brand-name">Harborline<br>Builders</span>
    </div>
    <div class="services">
      <p class="services-guarantee">Our services are<br>100% guaranteed</p>
      <p class="services-heading">Specializing in:</p>
      <ul class="service-list">
        <li class="service-item"><svg class="tick" viewBox="0 0 14 14"><circle cx="7" cy="7" r="6" fill="none" stroke="#e8202a" stroke-width="1.4"/><path d="M4 7.2l2 2 4-4.5" fill="none" stroke="#e8202a" stroke-width="1.6"/></svg>Remodel: Kitchen &amp; Bath</li>
        <li class="service-item"><svg class="tick" viewBox="0 0 14 14"><circle cx="7" cy="7" r="6" fill="none" stroke="#e8202a" stroke-width="1.4"/><path d="M4 7.2l2 2 4-4.5" fill="none" stroke="#e8202a" stroke-width="1.6"/></svg>Painting: Interior &amp; Exterior</li>
        <li class="service-item"><svg class="tick" viewBox="0 0 14 14"><circle cx="7" cy="7" r="6" fill="none" stroke="#e8202a" stroke-width="1.4"/><path d="M4 7.2l2 2 4-4.5" fill="none" stroke="#e8202a" stroke-width="1.6"/></svg>Flooring: Carpet, Vinyl, Wood</li>
        <li class="service-item"><svg class="tick" viewBox="0 0 14 14"><circle cx="7" cy="7" r="6" fill="none" stroke="#e8202a" stroke-width="1.4"/><path d="M4 7.2l2 2 4-4.5" fill="none" stroke="#e8202a" stroke-width="1.6"/></svg>Window &amp; Door Replacement</li>
        <li class="service-item"><svg class="tick" viewBox="0 0 14 14"><circle cx="7" cy="7" r="6" fill="none" stroke="#e8202a" stroke-width="1.4"/><path d="M4 7.2l2 2 4-4.5" fill="none" stroke="#e8202a" stroke-width="1.6"/></svg>Plumbing: Repairs &amp; Upgrades</li>
        <li class="service-item"><svg class="tick" viewBox="0 0 14 14"><circle cx="7" cy="7" r="6" fill="none" stroke="#e8202a" stroke-width="1.4"/><path d="M4 7.2l2 2 4-4.5" fill="none" stroke="#e8202a" stroke-width="1.6"/></svg>Energy-Efficient Upgrades</li>
        <li class="service-item"><svg class="tick" viewBox="0 0 14 14"><circle cx="7" cy="7" r="6" fill="none" stroke="#e8202a" stroke-width="1.4"/><path d="M4 7.2l2 2 4-4.5" fill="none" stroke="#e8202a" stroke-width="1.6"/></svg>Deck &amp; Patio Construction</li>
        <li class="service-item"><svg class="tick" viewBox="0 0 14 14"><circle cx="7" cy="7" r="6" fill="none" stroke="#e8202a" stroke-width="1.4"/><path d="M4 7.2l2 2 4-4.5" fill="none" stroke="#e8202a" stroke-width="1.6"/></svg>Water &amp; Mold Damage</li>
        <li class="service-item"><svg class="tick" viewBox="0 0 14 14"><circle cx="7" cy="7" r="6" fill="none" stroke="#e8202a" stroke-width="1.4"/><path d="M4 7.2l2 2 4-4.5" fill="none" stroke="#e8202a" stroke-width="1.6"/></svg>Garage Renovation</li>
      </ul>
    </div>
  </section>

  <section class="card card-back">
    <div class="person">
      <h1 class="person-name">Marcus Delling</h1>
      <p class="person-title">Licensed General Contractors</p>
    </div>
    <div class="divider"></div>
    <ul class="contact-list">
      <li class="contact-item"><svg class="contact-icon" viewBox="0 0 14 14"><path d="M3 1.5l2.2 2.6-1.2 1.5c.8 1.8 2.1 3.1 3.9 3.9l1.5-1.2 2.6 2.2-1.3 1.8C6 12 2 8 1.7 2.8z" fill="#e8202a"/></svg>858-471-6093</li>
      <li class="contact-item"><svg class="contact-icon" viewBox="0 0 14 14"><rect x="1" y="3" width="12" height="9" rx="1" fill="#e8202a"/><path d="M1.5 3.5L7 8l5.5-4.5" fill="none" stroke="#1f1f23" stroke-width="1.2"/></svg>info@brightoakbuilders.com</li>
      <li class="contact-item"><svg class="contact-icon" viewBox="0 0 14 14"><circle cx="7" cy="7" r="6" fill="#e8202a"/><path d="M1 7h12M7 1c-2.5 3-2.5 9 0 12M7 1c2.5 3 2.5 9 0 12" fill="none" stroke="#1f1f23" stroke-width="1"/></svg>www.brightoakbuilders.com</li>
    </ul>
    <p class="company">Harborline Builders Inc.</p>
  </section>

</main>
</body>
</html>
```